Progressive European Honey Business needs minimalistic packaging design

Hello - thank you for your interest in our brief. We are Honey Plinks, a London based Honey business, importing only the best honey Europe has to offer. Our values are deeply rooted with in progressive liberal values and we are looking for minimalist packaging, which reflects that.

We are looking for a design, which dimensions fit with our packaging option (Vessio Glass Jar | HEIGHT 90mm | DIAMETER 63mm). We will require a various output files (High Resolution JPEG (CMYK Colors 300 dpi) Source File Ai, PSD, PDF, Printing files (die cut, die folding) and a 3D Mockup of the packaging for use within digital commerce platforms.

We must be able to adjust the free text on the label front and it should include the following:
Brand Name
Honey type
Limited edition No. X / 100 ( X being the number of purchase i.e. 25 / 100)
EU Honey, Single Orgin (Germany)
(c) The net weight (250g)

The back must include room for additional information (again adjustable by us) and the following:
“Unsuitable for children under 12 months”
(b) The appropriate durability declaration

In total, we are looking for
a) A front label
b) A back label
c) A seal (round) including the attached bee and logo included in the Zip file.
Do note that a) & b) can also be combined into one design as long as the symmetry on the jar stays intact.

The final design should communicate modern aesthetics, high quality, that are slightly provocative and pop off the shelves.

Hi folks, sorry for the delay in completing this project, but my business partner had a leak in his house. We planned to finalise our review today, but this will have to wait until it's no longer raining in his livingroom. Our sincere apologies!

• See branding guidelines

• Must follow the branding guideline and fonts provided as attachment

```html
<!DOCTYPE html>
<html lang="en">
<head>
<meta charset="utf-8">
<title>Honey Plinks – Acacia Honey Front Label</title>
<link rel="stylesheet" href="https://fonts.googleapis.com/css2?family=Work+Sans:wght@300;600&display=swap">
<style>
  :root {
    --bg: #e8e8e8;
    --honey: #ec8e36;
    --honey-light: #f2a86a;
    --plum-edge: #574358;
    --plum-core: #1c141d;
    --label-text: #e4e4e6;
    --badge: #f0da3e;
    --badge-ink: #3a2f2a;
    --rule: #d4c23c;
  }
  html, body {
    margin: 0;
    width: 1200px;
    height: 960px;
    overflow: hidden;
    background: var(--bg);
  }
  .canvas {
    position: relative;
    width: 1200px;
    height: 960px;
  }
  .front-label {
    position: absolute;
    left: 181px;
    top: 34px;
    width: 837px;
    height: 891px;
  }
  .brand-name { font-family: "Work Sans", Arial, sans-serif; font-weight: 600; fill: var(--label-text); }
  .honey-type { font-family: "Work Sans", Arial, sans-serif; font-weight: 600; fill: var(--label-text); letter-spacing: 4px; }
  .origin { font-family: "Work Sans", Arial, sans-serif; font-weight: 300; fill: var(--label-text); }
  .net-weight { font-family: "Work Sans", Arial, sans-serif; font-weight: 600; fill: var(--label-text); }
  .badge-text { font-family: "Work Sans", Arial, sans-serif; font-weight: 600; fill: var(--badge-ink); }
</style>
</head>
<body>
<div class="canvas">
  <svg class="front-label" viewBox="0 0 620 660" xmlns="http://www.w3.org/2000/svg" aria-label="Honey Plinks front label">
    <defs>
      <linearGradient id="plum-fill" x1="0" y1="0" x2="1" y2="0">
        <stop offset="0" stop-color="var(--plum-edge)"/>
        <stop offset="0.5" stop-color="var(--plum-core)"/>
        <stop offset="1" stop-color="var(--plum-edge)"/>
      </linearGradient>
      <linearGradient id="honey-fill" x1="0" y1="0" x2="1" y2="0">
        <stop offset="0" stop-color="var(--honey-light)"/>
        <stop offset="0.45" stop-color="var(--honey)"/>
        <stop offset="1" stop-color="var(--honey-light)"/>
      </linearGradient>
    </defs>

    <rect class="honey-window" x="0" y="0" width="620" height="70" fill="url(#honey-fill)"
      role="img" aria-label="Honey showing through the glass above the label"/>

    <rect class="label-body" x="0" y="70" width="620" height="590" fill="url(#plum-fill)"/>

    <g class="edition-badge" transform="translate(65 160)">
      <circle r="46" fill="var(--badge)"/>
      <g transform="rotate(-15)">
        <text class="badge-text" x="0" y="-10" font-size="13" text-anchor="middle">LIMITED</text>
        <text class="badge-text" x="0" y="7" font-size="13" text-anchor="middle">EDITION</text>
        <text class="badge-text" x="0" y="23" font-size="10" text-anchor="middle">No. X / 100</text>
      </g>
    </g>

    <text class="brand-name" x="2" y="362" font-size="64">HONEY PLINKS</text>

    <text class="honey-type" x="2" y="553" font-size="30">Acacia Honey</text>
    <text class="origin" x="2" y="597" font-size="21">EU Honey ● Single Orgin (Germany)</text>
    <text class="net-weight" x="584" y="597" font-size="22" text-anchor="end">250g</text>

    <line class="base-rule" x1="0" y1="632" x2="620" y2="632" stroke="var(--rule)" stroke-width="2"/>
  </svg>
</div>
</body>
</html>
```